TalkHarbor - Language Coaching Services

Sleek, innovative, trendy design for Language Coaching business.

TalkHarbor is a new UK based company that provides Language Coaching services. We offer highly personalized on-line and face to face language courses. We also impart learning techniques workshops based on the latest neuroscience research for second-language acquisition.

Target Market(s)

See attached info

Industry/Entity Type

Consulting

Contact Information for Business Card

TalkHarbor
DaniaKV@talkharbor.co.uk
TalkHarbor.co.uk
London, UK

Font styles to use
Sans Serif

```html
<!DOCTYPE html>
<html lang="en">
<head>
<meta charset="utf-8">
<title>TalkHarbor – Business Card</title>
<link rel="stylesheet" href="https://fonts.googleapis.com/css2?family=Open+Sans:wght@400;600;700&display=swap">
<style>
  :root {
    --stage: #3a3a3b;
    --card: #29282a;
    --brand-blue: #1592cc;
    --band-blue: #0f94d0;
    --text-light: #f2f2f2;
    --font-body: "Open Sans", Arial, sans-serif;
  }
  * { box-sizing: border-box; margin: 0; padding: 0; }
  html, body {
    width: 1200px; height: 900px; overflow: hidden;
    background: var(--stage);
    font-family: var(--font-body);
  }
  .stage {
    position: relative; width: 1200px; height: 900px;
    display: flex; flex-direction: column; align-items: center;
    justify-content: center; gap: 44px;
  }
  .card {
    position: relative; width: 640px; height: 366px;
    background: var(--card);
    box-shadow: 0 10px 28px rgba(0,0,0,.45);
    overflow: hidden;
  }
  /* Front */
  .card--front {
    display: flex; flex-direction: column; align-items: center; justify-content: center;
  }
  .brand-mark {
    width: 70px; height: 70px; border-radius: 50%;
    border: 7px solid var(--brand-blue);
    margin-bottom: 14px;
  }
  .brand-name {
    font-family: var(--font-body); font-weight: 600;
    color: var(--brand-blue); letter-spacing: .02em; line-height: 1;
  }
  .card--front .brand-name { font-size: 58px; }
  .front-web {
    margin-top: 36px; color: var(--text-light);
    font-size: 17px; letter-spacing: .06em;
  }
  /* Back */
  .back-brand {
    position: absolute; left: 48px; top: 86px; width: 250px;
    display: flex; flex-direction: column; align-items: center;
  }
  .card--back .brand-mark { width: 62px; height: 62px; border-width: 6px; }
  .card--back .brand-name { font-size: 40px; }
  .contact {
    position: absolute; left: 336px; top: 70px; color: var(--text-light);
    font-size: 16px; line-height: 1.35; letter-spacing: .03em;
  }
  .contact-name { color: var(--brand-blue); font-weight: 700; font-size: 19px; }
  .contact-address { margin-bottom: 22px; }
  .contact-list { list-style: none; }
  .contact-list li { display: flex; align-items: center; gap: 16px; margin-bottom: 6px; }
  .contact-icon { width: 18px; height: 18px; flex: none; fill: var(--brand-blue); }
  .accent-band {
    position: absolute; left: 0; right: 0; bottom: 0; height: 22px;
    background: var(--band-blue);
  }
</style>
</head>
<body>
<main class="stage">
  <section class="card card--front" aria-label="Card front">
    <div class="brand-mark"></div>
    <div class="brand-name">TalkHarbor</div>
    <div class="front-web">www.talkharbor.co.uk</div>
  </section>

  <section class="card card--back" aria-label="Card back">
    <div class="back-brand">
      <div class="brand-mark"></div>
      <div class="brand-name">TalkHarbor</div>
    </div>
    <div class="contact">
      <p class="contact-name">TalkHarbor</p>
      <p class="contact-address">14 Harbour Lane, SE10 4RQ,<br>London, UK</p>
      <ul class="contact-list">
        <li>
          <svg class="contact-icon" viewBox="0 0 24 24" aria-hidden="true"><path d="M6.6 10.8a15.2 15.2 0 0 0 6.6 6.6l2.2-2.2a1 1 0 0 1 1-.25 11.4 11.4 0 0 0 3.6.57 1 1 0 0 1 1 1V20a1 1 0 0 1-1 1A17 17 0 0 1 3 4a1 1 0 0 1 1-1h3.5a1 1 0 0 1 1 1c0 1.25.2 2.45.57 3.57a1 1 0 0 1-.25 1z"/></svg>
          <span>+44 1632 960218</span>
        </li>
        <li>
          <svg class="contact-icon" viewBox="0 0 24 24" aria-hidden="true"><path d="M2 5h20v14H2z M3.5 6.5 12 13l8.5-6.5" stroke="#29282a" stroke-width="1.4"/></svg>
          <span>daniakv@talkharbor.co.uk</span>
        </li>
        <li>
          <svg class="contact-icon" viewBox="0 0 24 24" aria-hidden="true"><circle cx="12" cy="12" r="10"/><path d="M2 12h20M12 2c3 3 3 17 0 20M12 2c-3 3-3 17 0 20M4 7h16M4 17h16" stroke="#29282a" stroke-width="1.2" fill="none"/></svg>
          <span>www.talkharbor.co.uk</span>
        </li>
      </ul>
    </div>
    <div class="accent-band"></div>
  </section>
</main>
</body>
</html>
```